Veluxa Bone & Motion Business Card

Need a business card using the logo provided. I want brand side of the card to be grey with the logo in the center of the card in white.

On the other side I leave to the designers

Target Market(s)

Personal Injury Attorneys

Industry/Entity Type

Medical

Contact Information for Business Card

Name, CEO. Cell Phone, (Hialeah, Address, Phone) (Homestead, Address, Phone) (Tallahassee, Address, Phone)

Colors

Designer to choose only greyscale colors for use in the design.

Requirements
Must have
• Logo by itself on one side

```html
<!DOCTYPE html>
<html lang="en">
<head>
<meta charset="utf-8">
<title>Veluxa Bone &amp; Motion Business Card</title>
<link href="https://fonts.googleapis.com/css2?family=Lato:wght@400;700&family=Montserrat:wght@400;600&display=swap" rel="stylesheet">
<style>
  :root {
    --backdrop: #b1b1b1;
    --card: #9bb6be;
    --panel: #ffffff;
    --ink: #111111;
    --tab: #5f7f87;
    --tab-fold: #455f66;
    --accent: #9bb6be;
    --white: #ffffff;
  }
  * { margin: 0; padding: 0; box-sizing: border-box; }
  html, body { width: 1200px; height: 2942px; overflow: hidden; }
  body { background: var(--backdrop); position: relative; font-family: "Montserrat", sans-serif; }

  .card {
    position: absolute; left: 62px; width: 1076px; height: 614px;
    background: var(--card);
    box-shadow: 0 6px 10px rgba(0,0,0,.35);
    overflow: hidden;
  }
  .card--front { top: 1328px; }
  .card--back { top: 2092px; }

  .wordmark {
    position: absolute; color: var(--white);
    font-family: "Lato", sans-serif; font-weight: 700;
    text-align: center; line-height: 1;
  }
  .wordmark__name { display: block; letter-spacing: .16em; }
  .wordmark__sub { display: block; letter-spacing: .2em; }

  .card--front .wordmark { left: 0; right: 0; top: 218px; }
  .card--front .wordmark__name { font-size: 96px; }
  .card--front .wordmark__sub { font-size: 48px; margin-top: 28px; }

  .card--back .wordmark { left: 40px; width: 440px; top: 258px; }
  .card--back .wordmark__name { font-size: 62px; }
  .card--back .wordmark__sub { font-size: 32px; margin-top: 18px; }

  .contact-panel {
    position: absolute; left: 515px; top: 0; width: 472px; height: 100%;
    background: var(--panel);
  }
  .person { position: absolute; left: 40px; top: 56px; }
  .person__name { font-size: 40px; font-weight: 400; color: var(--ink); letter-spacing: .01em; }
  .person__role { font-size: 23px; color: var(--accent); margin-top: 2px; }

  .office { position: absolute; left: -11px; }
  .office--1 { top: 206px; }
  .office--2 { top: 337px; }
  .office--3 { top: 465px; }
  .office__tab {
    position: relative; display: inline-block;
    background: var(--tab); color: var(--white);
    font-size: 23px; line-height: 27px; padding: 0 18px 0 33px;
    min-width: 137px;
  }
  .office__tab::before {
    content: ""; position: absolute; left: 0; top: -8px;
    border-left: 11px solid transparent; border-bottom: 8px solid var(--tab-fold);
  }
  .office__line {
    display: flex; align-items: center; gap: 10px;
    margin-left: 48px; margin-top: 6px;
    font-size: 23px; font-weight: 600; color: var(--ink); line-height: 26px;
  }
  .office__line svg { width: 18px; height: 18px; flex: none; }
</style>
</head>
<body>

<section class="card card--front" aria-label="Card front">
  <div class="wordmark">
    <span class="wordmark__name">VELUXA</span>
    <span class="wordmark__sub">BONE &amp; MOTION</span>
  </div>
</section>

<section class="card card--back" aria-label="Card back">
  <div class="wordmark">
    <span class="wordmark__name">VELUXA</span>
    <span class="wordmark__sub">BONE &amp; MOTION</span>
  </div>

  <div class="contact-panel">
    <div class="person">
      <p class="person__name">DR. MARCUS HALDEN</p>
      <p class="person__role">CEO</p>
    </div>

    <div class="office office--1">
      <span class="office__tab">Hialeah</span>
      <p class="office__line"><svg viewBox="0 0 24 24"><path d="M6.6 10.8a15 15 0 0 0 6.6 6.6l2.2-2.2a1 1 0 0 1 1-.25 11.4 11.4 0 0 0 3.6.57 1 1 0 0 1 1 1V20a1 1 0 0 1-1 1A17 17 0 0 1 3 4a1 1 0 0 1 1-1h3.5a1 1 0 0 1 1 1c0 1.25.2 2.45.57 3.57a1 1 0 0 1-.25 1z" fill="none" stroke="#9bb6be" stroke-width="2"/></svg>305-218-447</p>
      <p class="office__line"><svg viewBox="0 0 24 24"><path d="M12 2a7 7 0 0 0-7 7c0 5 7 13 7 13s7-8 7-13a7 7 0 0 0-7-7z" fill="none" stroke="#9bb6be" stroke-width="2.4"/><circle cx="12" cy="9" r="2.5" fill="#9bb6be"/></svg>418/3 Coral Palm St,</p>
    </div>

    <div class="office office--2">
      <span class="office__tab">Homestead</span>
      <p class="office__line"><svg viewBox="0 0 24 24"><path d="M6.6 10.8a15 15 0 0 0 6.6 6.6l2.2-2.2a1 1 0 0 1 1-.25 11.4 11.4 0 0 0 3.6.57 1 1 0 0 1 1 1V20a1 1 0 0 1-1 1A17 17 0 0 1 3 4a1 1 0 0 1 1-1h3.5a1 1 0 0 1 1 1c0 1.25.2 2.45.57 3.57a1 1 0 0 1-.25 1z" fill="none" stroke="#9bb6be" stroke-width="2"/></svg>305-642-190</p>
      <p class="office__line"><svg viewBox="0 0 24 24"><path d="M12 2a7 7 0 0 0-7 7c0 5 7 13 7 13s7-8 7-13a7 7 0 0 0-7-7z" fill="none" stroke="#9bb6be" stroke-width="2.4"/><circle cx="12" cy="9" r="2.5" fill="#9bb6be"/></svg>227/5 Redland Ave,</p>
    </div>

    <div class="office office--3">
      <span class="office__tab">Tallahassee</span>
      <p class="office__line"><svg viewBox="0 0 24 24"><path d="M6.6 10.8a15 15 0 0 0 6.6 6.6l2.2-2.2a1 1 0 0 1 1-.25 11.4 11.4 0 0 0 3.6.57 1 1 0 0 1 1 1V20a1 1 0 0 1-1 1A17 17 0 0 1 3 4a1 1 0 0 1 1-1h3.5a1 1 0 0 1 1 1c0 1.25.2 2.45.57 3.57a1 1 0 0 1-.25 1z" fill="none" stroke="#9bb6be" stroke-width="2"/></svg>850-376-512</p>
      <p class="office__line"><svg viewBox="0 0 24 24"><path d="M12 2a7 7 0 0 0-7 7c0 5 7 13 7 13s7-8 7-13a7 7 0 0 0-7-7z" fill="none" stroke="#9bb6be" stroke-width="2.4"/><circle cx="12" cy="9" r="2.5" fill="#9bb6be"/></svg>316/2 Oakmoor St,</p>
    </div>
  </div>
</section>

</body>
</html>
```